Business Card Design Project

Business Card
We are rebranding with a new logo
Industry/Entity Type
Business
Contact Information for Business Card
Dennis Morvale +61 487215963 dennis@quorv.com.au P.O. Box 872 Fernlow QLD 4309
Requirements
Must have
- Logo

```html
<!DOCTYPE html>
<html lang="en">
<head>
<meta charset="utf-8">
<title>Quorv International – Business Card</title>
<link rel="stylesheet" href="https://fonts.googleapis.com/css2?family=Open+Sans:wght@400;700&display=swap">
<style>
  :root {
    --backdrop: #0b0b0b;
    --card: #fbf9f5;
    --blue: #2f8fc6;
    --blue-deep: #1f6d9e;
    --blue-light: #3fa9dc;
    --orange: #f39a33;
    --orange-deep: #e8692e;
    --ink: #151515;
    --text: #3a3a3a;
  }
  * { box-sizing: border-box; margin: 0; padding: 0; }
  html, body {
    width: 1200px; height: 1000px; overflow: hidden;
    background: var(--backdrop);
    font-family: "Open Sans", Arial, sans-serif;
  }
  .canvas {
    width: 1200px; height: 1000px;
    display: flex; align-items: center; justify-content: center; gap: 40px;
  }
  .card {
    position: relative;
    width: 540px; height: 320px;
    background: var(--card);
    border-radius: 22px;
    overflow: hidden;
  }
  .card__sweep { position: absolute; }
  .card--back .card__sweep {
    left: 40px; top: 24px; width: 380px; height: 140px;
    border-radius: 0 0 140px 0;
    background: linear-gradient(120deg, var(--orange) 0%, var(--orange-deep) 22%, var(--blue-deep) 40%, var(--blue-light) 100%);
  }
  .card--front .card__sweep {
    left: 0; bottom: 0; width: 250px; height: 140px;
    border-radius: 0 140px 0 0;
    background: linear-gradient(60deg, var(--blue-light) 0%, var(--blue-deep) 60%, var(--orange-deep) 85%, var(--orange) 100%);
  }
  .brand {
    position: absolute;
    display: flex; align-items: center; gap: 10px;
    font-weight: 700; font-size: 24px; color: var(--blue);
    line-height: 1.1;
  }
  .brand__dot {
    width: 22px; height: 22px; border-radius: 50%;
    background: var(--orange);
    flex: none;
  }
  .card--back .brand { right: 50px; bottom: 48px; }
  .card--front .brand { left: 40px; top: 40px; }
  .contact {
    position: absolute; left: 282px; bottom: 40px;
    width: 230px;
  }
  .contact__name {
    font-weight: 700; font-size: 18px; color: var(--ink);
    letter-spacing: 0.3px; margin-bottom: 12px;
  }
  .contact__row {
    display: flex; align-items: flex-start; gap: 8px;
    font-size: 14px; color: var(--text); line-height: 1.3;
    margin-bottom: 6px;
  }
  .contact__icon {
    width: 18px; height: 18px; flex: none; margin-top: 1px;
  }
</style>
</head>
<body>
<main class="canvas">
  <section class="card card--back" aria-label="Card back">
    <div class="card__sweep" role="img" aria-label="Sweeping blue and orange brand swoosh"></div>
    <div class="brand"><span class="brand__dot"></span>Quorv International</div>
  </section>

  <section class="card card--front" aria-label="Card front">
    <div class="brand"><span class="brand__dot"></span>Quorv International</div>
    <div class="card__sweep" role="img" aria-label="Sweeping blue and orange brand swoosh"></div>
    <div class="contact">
      <p class="contact__name">DENNIS MORVALE</p>
      <p class="contact__row">
        <svg class="contact__icon" viewBox="0 0 18 18" aria-hidden="true"><circle cx="9" cy="9" r="9" fill="var(--orange-deep)"/><path d="M6.3 4.8l1.5 1.6-.8 1.2a5 5 0 0 0 3.4 3.4l1.2-.8 1.6 1.5-.9 1.4c-3.5-.3-6.6-3.4-6.9-6.9z" fill="#fff"/></svg>
        +61 487215963
      </p>
      <p class="contact__row">
        <svg class="contact__icon" viewBox="0 0 18 18" aria-hidden="true"><circle cx="9" cy="9" r="9" fill="var(--orange-deep)"/><rect x="4.5" y="6" width="9" height="6.2" rx="1" fill="#fff"/><path d="M4.8 6.4L9 9.4l4.2-3" stroke="var(--orange-deep)" stroke-width="1" fill="none"/></svg>
        dennis@quorv.com.au
      </p>
      <p class="contact__row">
        <svg class="contact__icon" viewBox="0 0 18 18" aria-hidden="true"><circle cx="9" cy="9" r="9" fill="var(--orange-deep)"/><path d="M9 4a3.4 3.4 0 0 0-3.4 3.4C5.6 10 9 14 9 14s3.4-4 3.4-6.6A3.4 3.4 0 0 0 9 4z" fill="#fff"/><circle cx="9" cy="7.4" r="1.3" fill="var(--orange-deep)"/></svg>
        <span>P.O. Box 872 Fernlow<br>QLD 4309</span>
      </p>
    </div>
  </section>
</main>
</body>
</html>
```